Blind Rivet Product catalogue

Need a design in wordpress with a productcatalogue where i present all products. This is a B2B business. The products is Blindrivets and Blindrivet nuts and accessories to this. I only want the basic information and also technical specification.

This is a subcompany to my existing company k7.m3.se but specializing in a subcategory

Businesses using blind rivet technology.

Industrial

Sans Serif

Must have
• Three different categories for the products; Blind Rivets - Blind Rivet Nut - Riveting Tools
Nice to have
• Possible to ad login for more information of the different sizes

```html
<!DOCTYPE html>
<html lang="en">
<head>
<meta charset="utf-8">
<title>Blind Rivet Catalogue – Dark and Light Themes</title>
<link href="https://fonts.googleapis.com/css2?family=Montserrat:wght@400;500;600;700&display=swap" rel="stylesheet">
<style>
:root{
  --green:#76c442;
  --red:#d7262b;
  --black:#000;
  --white:#fff;
  --gold:#f0b531;
  --grey-line:#d9d9d9;
  --stage:#f0f0f0;
}
*{box-sizing:border-box;margin:0;padding:0}
html,body{width:1185px;height:1200px;overflow:hidden;background:var(--stage)}
body{font-family:'Montserrat',sans-serif}
.stage{position:absolute;left:0;top:0;width:1908px;height:1932px;transform:scale(.6211);transform-origin:0 0;background:var(--stage)}
.page{position:absolute;top:36px;width:900px;height:1860px;overflow:hidden;background:var(--bg);color:var(--ink)}
.page--dark{left:35px;--bg:#000;--ink:#fff;--muted:#fff;--nav:#fff;--side-bg:#000;--side-border:#fff;--side-line:#555}
.page--light{left:965px;--bg:#fff;--ink:#111;--muted:#555;--nav:#222;--side-bg:#fff;--side-border:#e4e4e4;--side-line:#e4e4e4}
.abs{position:absolute}
/* top bar */
.topbar{left:0;top:0;width:900px;height:29px;background:var(--green);color:#fff;font-size:12px;font-weight:500}
.topbar span{position:absolute;top:8px;display:flex;align-items:center;gap:6px}
/* header */
.header{left:0;top:29px;width:900px;height:71px;background:#000;color:#fff}
.brand{position:absolute;left:83px;top:22px;display:flex;align-items:center;gap:7px;font-size:21px;font-weight:700;letter-spacing:1px;color:#fff}
.brand i{width:14px;height:14px;background:var(--green);display:block}
.search{position:absolute;left:341px;top:17px;width:317px;height:38px;background:#fff;border-radius:19px;overflow:hidden;font-size:11px;color:#777}
.search .q{position:absolute;left:21px;top:13px}
.search .cat{position:absolute;left:156px;top:13px}
.search .btn{position:absolute;right:0;top:0;width:45px;height:38px;background:var(--red);border-radius:0 19px 19px 0;display:flex;align-items:center;justify-content:center}
.hicon{position:absolute;top:14px;text-align:center;font-size:11px;font-weight:500;color:#fff}
.hicon svg{display:block;margin:0 auto 2px}
.badge{position:absolute;top:-2px;right:-2px;width:10px;height:10px;border-radius:50%;background:var(--red);font-size:7px;line-height:10px}
/* hero */
.hero{left:0;top:100px;width:900px;height:345px}
.hero-photo{position:absolute;inset:0}
.page--dark .hero-photo{background:linear-gradient(180deg,#8b97a0 0%,#b79258 35%,#8c6128 65%,#4e351a 100%)}
.page--light .hero-photo{background:linear-gradient(180deg,#fff 0%,#f2f3f1 30%,#9ea49b 50%,#5b5a52 75%,#3b3833 100%)}
.hero-tool{position:absolute;left:700px;top:115px;width:170px;height:240px;border-radius:40px 60px 30px 20px;background:linear-gradient(160deg,#3a3e4a,#15161b)}
.nav{position:absolute;left:0;top:18px;width:900px;display:flex;justify-content:center;gap:23px;font-size:13px;font-weight:500;color:var(--nav)}
.nav .sep{font-weight:400}
.nav .on{color:var(--red);border-bottom:2px solid var(--red);padding-bottom:3px}
.hero h1{position:absolute;left:0;top:155px;width:900px;text-align:center;font-size:25px;font-weight:700;color:#fff;letter-spacing:.2px}
.shop-now{position:absolute;left:392px;top:189px;width:117px;height:37px;border-radius:19px;background:var(--red);color:#fff;font-size:13px;font-weight:600;text-align:center;line-height:37px}
/* welcome */
.rule{left:433px;top:498px;width:34px;height:2px;background:var(--green)}
.welcome{left:0;top:510px;width:900px;text-align:center;font-size:26px;font-weight:700;color:var(--ink)}
.intro{left:95px;top:553px;width:710px;text-align:center;font-size:11px;line-height:21.2px;color:var(--muted)}
/* category tiles */
.tile{top:693px;width:240px;height:170px;border:1px solid #5a8f3a}
.tile .pic{position:absolute;inset:0}
.tile .pill{position:absolute;left:50%;top:67px;transform:translateX(-50%);height:34px;padding:0 23px;border-radius:17px;background:var(--red);color:#fff;font-size:12px;font-weight:600;line-height:34px;white-space:nowrap}
.pic-rivets{background:linear-gradient(135deg,#3a3a3a,#9b9b9b 40%,#4a4a4a 70%,#a8a8a8)}
.pic-nuts{background:linear-gradient(135deg,#555,#8d8d8d 50%,#3f3f3f)}
.pic-tools{background:linear-gradient(135deg,#6a6d72,#2f3033 60%,#141415)}
/* sidebar */
.side{left:83px;top:934px;width:182px;height:358px;background:var(--side-bg);border:1px solid var(--side-border)}
.side-head{height:44px;background:var(--green);color:#fff;font-size:15px;font-weight:600;text-align:center;line-height:44px;margin:-1px -1px 0}
.side-search{position:relative;margin:9px 5px 0 5px;height:30px;border:1px solid #ddd;border-radius:15px;background:#fff;font-size:10px;color:#888;padding:9px 0 0 12px}
.side-search b{position:absolute;right:2px;top:2px;width:24px;height:24px;border-radius:50%;background:var(--red)}
.side ul{list-style:none;margin-top:8px}
.side li{height:39px;line-height:39px;padding-left:17px;font-size:12px;font-weight:500;color:var(--ink);border-top:1px solid var(--side-line);margin:0 3px}
.side li:first-child{border-top:0;color:var(--red)}
/* products */
.feat-line{top:946px;height:1px;background:var(--green)}
.feat-title{left:445px;top:935px;font-size:18px;font-weight:700;color:var(--ink)}
.card{width:176px;height:297px;background:#fff;border:1px solid #e6e6e6;color:#111}
.card .sku{position:absolute;left:8px;top:8px;font-size:11px;color:#444}
.card .heart{position:absolute;right:7px;top:8px}
.card .pic{position:absolute;left:20px;top:36px;width:136px;height:150px;border-radius:8px}
.pic-gun{background:radial-gradient(circle at 50% 45%,#3b3f4c 0 38%,#e9e9e9 39% 52%,#fff 53%)}
.pic-pin{background:linear-gradient(90deg,#fff 44%,#b6b9bb 46% 54%,#fff 56%)}
.pic-rivet{background:radial-gradient(ellipse at 50% 50%,#9a9ea2 0 18%,#e6e6e6 19% 34%,#fff 36%)}
.pic-nut{background:radial-gradient(circle at 55% 45%,#c9cbcd 0 30%,#e9e9e9 31% 45%,#fff 47%)}
.pic-plier{background:radial-gradient(ellipse at 50% 50%,#e84a22 0 25%,#262626 26% 34%,#fff 36%)}
.card .name{position:absolute;left:0;top:209px;width:176px;text-align:center;font-size:12px;font-weight:500}
.card .stars{position:absolute;left:0;top:225px;width:176px;text-align:center;color:var(--gold);font-size:14px;letter-spacing:-1px}
.card .bar{position:absolute;left:-1px;bottom:-1px;width:176px;height:34px;display:flex}
.qty{width:56px;background:var(--green);display:flex;color:#fff;font-size:13px}
.qty span{flex:1;text-align:center;line-height:34px;border-right:1px solid rgba(255,255,255,.5)}
.add{flex:1;background:var(--red);color:#fff;font-size:11px;font-weight:600;display:flex;align-items:center;justify-content:center;gap:4px}
/* footer */
.footer{left:0;top:1646px;width:900px;height:214px;background:#000;color:#fff}
.fcol{position:absolute;top:50px}
.fcol h4{font-size:12px;font-weight:600;margin-bottom:9px}
.fcol p{font-size:10.5px;line-height:21px}
.fdiv{position:absolute;left:83px;top:166px;width:734px;height:1px;background:#444}
.copy{position:absolute;left:359px;top:184px;font-size:11px}
.pay{position:absolute;top:183px;width:29px;height:16px;background:#e9e9e9;border-radius:2px}
</style>
</head>
<body>
<div class="stage">

<!-- DARK THEME -->
<div class="page page--dark">
  <div class="abs topbar">
    <span style="left:82px"><svg width="10" height="10" viewBox="0 0 24 24"><path fill="#fff" d="M6.6 10.8a15 15 0 006.6 6.6l2.2-2.2c.3-.3.7-.4 1-.2 1.1.4 2.3.6 3.6.6.6 0 1 .4 1 1V20c0 .6-.4 1-1 1A17 17 0 013 4c0-.6.4-1 1-1h3.5c.6 0 1 .4 1 1 0 1.3.2 2.5.6 3.6.1.3 0 .7-.2 1z"/></svg>Call Us : +45 20 11 48 90</span>
    <span style="left:360px"><svg width="26" height="14" viewBox="0 0 26 14"><path fill="#fff" d="M1 1h15v9H1zM17 4h5l3 3v3h-8z"/><circle cx="6" cy="12" r="2" fill="#fff"/><circle cx="20" cy="12" r="2" fill="#fff"/></svg>&nbsp;FREE SHIPPING OVER $50</span>
    <span style="left:690px"><svg width="11" height="11" viewBox="0 0 24 24"><circle cx="12" cy="12" r="10" fill="#fff"/></svg>Language : English ▾</span>
  </div>
  <div class="abs header">
    <div class="brand"><i></i>K7M3</div>
    <div class="search"><span class="q">Search Products</span><span class="cat">|&nbsp;&nbsp;&nbsp;All Categories</span><span class="btn"><svg width="18" height="18" viewBox="0 0 24 24" fill="none" stroke="#fff" stroke-width="2.2"><circle cx="10" cy="10" r="7"/><path d="M15 15l6 6"/></svg></span></div>
    <div class="hicon" style="left:694px"><svg width="26" height="28" viewBox="0 0 26 28" fill="none" stroke="#fff" stroke-width="1.8"><circle cx="13" cy="9" r="7"/><path d="M2 27c0-7 5-10 11-10s11 3 11 10z"/></svg>My Account</div>
    <div class="hicon" style="left:775px"><div style="position:relative;width:30px;margin:0 auto"><svg width="30" height="28" viewBox="0 0 30 28" fill="none" stroke="#fff" stroke-width="1.8"><path d="M1 3h5l4 15h15l3-11H8"/><circle cx="12" cy="24" r="2"/><circle cx="23" cy="24" r="2"/></svg><span class="badge">3</span></div>My Cart</div>
  </div>
  <div class="abs hero">
    <div class="hero-photo" role="img" aria-label="Wooden boardwalk through golden grass dunes"></div>
    <div class="hero-tool" role="img" aria-label="Cordless battery-driven riveting tool"></div>
    <nav class="nav"><span class="on">SHOP</span><span class="sep">|</span><span>ABOUT</span><span class="sep">|</span><span>LOGIN</span><span class="sep">|</span><span>DEALS</span><span class="sep">|</span><span>WHOLESALE</span><span class="sep">|</span><span>CATALOGUE</span><span class="sep">|</span><span>CONTACT</span></nav>
    <h1>BLINDRIVETS &amp; BLINDRIVET NUTS</h1>
    <div class="shop-now">SHOP NOW</div>
  </div>
  <div class="abs rule"></div>
  <h2 class="abs welcome">WELCOME TO BLINDRIVETS</h2>
  <p class="abs intro">Lorem ipsum dolor sit amet, consectetur adipiscing elit, sed do eiusmod tempor incididunt ut labore et dolore magna aliqua. Quis ipsum suspendisse ultrices gravida. Risus commodo viverra maecenas accumsan lacus vel facilisis. Lorem ipsum dolor sit amet, conseadipiscing elit, sed do eiusmod tempor incididunt ut labore et dolore magna aliqua. Quis ipsum suspendisse ultrices gravida. Risus commodo viverra maecenas accumsan lacus vel facilisis.</p>
  <div class="abs tile" style="left:83px"><div class="pic pic-rivets" role="img" aria-label="Pile of aluminium blind rivets"></div><span class="pill">Blind Rivets</span></div>
  <div class="abs tile" style="left:330px"><div class="pic pic-nuts" role="img" aria-label="Pile of steel blind rivet nuts"></div><span class="pill">Blind Rivet Nut</span></div>
  <div class="abs tile" style="left:576px"><div class="pic pic-tools" role="img" aria-label="Hand riveting tool with nosepieces"></div><span class="pill">Riveting Tools</span></div>
  <div class="abs side"><div class="side-head">CATEGORIES</div><div class="side-search">search wines<b></b></div><ul><li>ALL</li><li>BLIND RIVETS</li><li>BLIND RIVET NUT</li><li>RIVETING TOOLS</li><li>LOREM IPSUM SED</li><li>LOREM IPSUM SED</li><li>LOREM IPSUM SED</li></ul></div>
  <div class="abs feat-line" style="left:294px;width:140px"></div>
  <div class="abs feat-title">FEATURED PRODUCTS</div>
  <div class="abs feat-line" style="left:675px;width:142px"></div>
  <div class="abs card" style="left:272px;top:977px"><span class="sku"># 12242</span><svg class="heart" width="14" height="12" viewBox="0 0 24 21"><path fill="#ddd" d="M12 21L2 11A6 6 0 0112 3a6 6 0 0110 8z"/></svg><div class="pic pic-gun" role="img" aria-label="Battery-driven rivet tool"></div><div class="name">Battery-Driven</div><div class="stars">★★★★★</div><div class="bar"><div class="qty"><span>–</span><span>1</span><span style="border:0">+</span></div><div class="add">🛒 ADD TO CART</div></div></div>
  <div class="abs card" style="left:456px;top:977px"><span class="sku"># 12242</span><svg class="heart" width="14" height="12" viewBox="0 0 24 21"><path fill="#ddd" d="M12 21L2 11A6 6 0 0112 3a6 6 0 0110 8z"/></svg><div class="pic pic-rivet" role="img" aria-label="Single blind rivet"></div><div class="name">blind-rivets</div><div class="stars">★★★★★</div><div class="bar"><div class="qty"><span>–</span><span>1</span><span style="border:0">+</span></div><div class="add">🛒 ADD TO CART</div></div></div>
  <div class="abs card" style="left:640px;top:977px"><span class="sku"># 12242</span><svg class="heart" width="14" height="12" viewBox="0 0 24 21"><path fill="#ddd" d="M12 21L2 11A6 6 0 0112 3a6 6 0 0110 8z"/></svg><div class="pic pic-nut" role="img" aria-label="Knurled blind rivet nut"></div><div class="name">blind-rivet-nut</div><div class="stars">★★★★★</div><div class="bar"><div class="qty"><span>–</span><span>1</span><span style="border:0">+</span></div><div class="add">🛒 ADD TO CART</div></div></div>
  <div class="abs card" style="left:272px;top:1281px"><span class="sku"># 12242</span><svg class="heart" width="14" height="12" viewBox="0 0 24 21"><path fill="#ddd" d="M12 21L2 11A6 6 0 0112 3a6 6 0 0110 8z"/></svg><div class="pic pic-pin" role="img" aria-label="Blind rivet with mandrel"></div><div class="name">Battery-Driven</div><div class="stars">★★★★★</div><div class="bar"><div class="qty"><span>–</span><span>1</span><span style="border:0">+</span></div><div class="add">🛒 ADD TO CART</div></div></div>
  <div class="abs card" style="left:456px;top:1281px"><span class="sku"># 12242</span><svg class="heart" width="14" height="12" viewBox="0 0 24 21"><path fill="#ddd" d="M12 21L2 11A6 6 0 0112 3a6 6 0 0110 8z"/></svg><div class="pic pic-plier" role="img" aria-label="Orange hand riveter pliers"></div><div class="name">Battery-Driven</div><div class="stars">★★★★★</div><div class="bar"><div class="qty"><span>–</span><span>1</span><span style="border:0">+</span></div><div class="add">🛒 ADD TO CART</div></div></div>
  <div class="abs card" style="left:640px;top:1281px"><span class="sku"># 12242</span><svg class="heart" width="14" height="12" viewBox="0 0 24 21"><path fill="#ddd" d="M12 21L2 11A6 6 0 0112 3a6 6 0 0110 8z"/></svg><div class="pic pic-gun" role="img" aria-label="Battery-driven rivet tool"></div><div class="name">Battery-Driven</div><div class="stars">★★★★★</div><div class="bar"><div class="qty"><span>–</span><span>1</span><span style="border:0">+</span></div><div class="add">🛒 ADD TO CART</div></div></div>
  <footer class="abs footer">
    <div class="fcol" style="left:83px"><h4>INFORMATION</h4><p>About Us<br>Contact US<br>Terms Of Use<br>Privacy Policy</p></div>
    <div class="fcol" style="left:257px"><h4>CONTACT &amp; SUPPORT</h4><p>sales and support:<br>+ 45 20 11 48 90<br>+ 45 20 11 48 91<br>E-mail: rivetline.example</p></div>
    <div class="fcol" style="left:471px"><h4>WHY CHOOSE US</h4><p>Product Recall<br>Gift Vouchers<br>Returns And Exchanges<br>Shipping Options</p></div>
    <div class="fcol" style="left:675px"><h4>POPULAR CATEGORY</h4><p>Lorem ipsum dolor sit amet,<br>Lorem ipsum dolor sit amet,<br>Lorem ipsum amet,<br>Lorem ipsum &nbsp;sit amet,</p></div>
    <div class="fdiv"></div>
    <div class="copy">Copyright © 2020. All Rights Reserved</div>
    <span class="pay" style="left:616px"></span><span class="pay" style="left:650px"></span><span class="pay" style="left:684px"></span><span class="pay" style="left:718px"></span><span class="pay" style="left:752px"></span><span class="pay" style="left:786px"></span>
  </footer>
</div>

<!-- LIGHT THEME -->
<div class="page page--light">
  <div class="abs topbar">
    <span style="left:82px"><svg width="10" height="10" viewBox="0 0 24 24"><path fill="#fff" d="M6.6 10.8a15 15 0 006.6 6.6l2.2-2.2c.3-.3.7-.4 1-.2 1.1.4 2.3.6 3.6.6.6 0 1 .4 1 1V20c0 .6-.4 1-1 1A17 17 0 013 4c0-.6.4-1 1-1h3.5c.6 0 1 .4 1 1 0 1.3.2 2.5.6 3.6.1.3 0 .7-.2 1z"/></svg>Call Us : +45 20 11 48 90</span>
    <span style="left:360px"><svg width="26" height="14" viewBox="0 0 26 14"><path fill="#fff" d="M1 1h15v9H1zM17 4h5l3 3v3h-8z"/><circle cx="6" cy="12" r="2" fill="#fff"/><circle cx="20" cy="12" r="2" fill="#fff"/></svg>&nbsp;FREE SHIPPING OVER $50</span>
    <span style="left:690px"><svg width="11" height="11" viewBox="0 0 24 24"><circle cx="12" cy="12" r="10" fill="#fff"/></svg>Language : English ▾</span>
  </div>
  <div class="abs header">
    <div class="brand"><i></i>K7M3</div>
    <div class="search"><span class="q">Search Products</span><span class="cat">|&nbsp;&nbsp;&nbsp;All Categories</span><span class="btn"><svg width="18" height="18" viewBox="0 0 24 24" fill="none" stroke="#fff" stroke-width="2.2"><circle cx="10" cy="10" r="7"/><path d="M15 15l6 6"/></svg></span></div>
    <div class="hicon" style="left:694px"><svg width="26" height="28" viewBox="0 0 26 28" fill="none" stroke="#fff" stroke-width="1.8"><circle cx="13" cy="9" r="7"/><path d="M2 27c0-7 5-10 11-10s11 3 11 10z"/></svg>My Account</div>
    <div class="hicon" style="left:775px"><div style="position:relative;width:30px;margin:0 auto"><svg width="30" height="28" viewBox="0 0 30 28" fill="none" stroke="#fff" stroke-width="1.8"><path d="M1 3h5l4 15h15l3-11H8"/><circle cx="12" cy="24" r="2"/><circle cx="23" cy="24" r="2"/></svg><span class="badge">3</span></div>My Cart</div>
  </div>
  <div class="abs hero">
    <div class="hero-photo" role="img" aria-label="Weathered wooden pier over a misty lake"></div>
    <div class="hero-tool" role="img" aria-label="Cordless battery-driven riveting tool"></div>
    <nav class="nav"><span class="on">SHOP</span><span class="sep">|</span><span>ABOUT</span><span class="sep">|</span><span>LOGIN</span><span class="sep">|</span><span>DEALS</span><span class="sep">|</span><span>WHOLESALE</span><span class="sep">|</span><span>CATALOGUE</span><span class="sep">|</span><span>CONTACT</span></nav>
    <h1>BLINDRIVETS &amp; BLINDRIVET NUTS</h1>
    <div class="shop-now">SHOP NOW</div>
  </div>
  <div class="abs rule"></div>
  <h2 class="abs welcome">WELCOME TO BLINDRIVETS</h2>
  <p class="abs intro">Lorem ipsum dolor sit amet, consectetur adipiscing elit, sed do eiusmod tempor incididunt ut labore et dolore magna aliqua. Quis ipsum suspendisse ultrices gravida. Risus commodo viverra maecenas accumsan lacus vel facilisis. Lorem ipsum dolor sit amet, conseadipiscing elit, sed do eiusmod tempor incididunt ut labore et dolore magna aliqua. Quis ipsum suspendisse ultrices gravida. Risus commodo viverra maecenas accumsan lacus vel facilisis.</p>
  <div class="abs tile" style="left:83px"><div class="pic pic-rivets" role="img" aria-label="Pile of aluminium blind rivets"></div><span class="pill">Blind Rivets</span></div>
  <div class="abs tile" style="left:330px"><div class="pic pic-nuts" role="img" aria-label="Pile of steel blind rivet nuts"></div><span class="pill">Blind Rivet Nut</span></div>
  <div class="abs tile" style="left:576px"><div class="pic pic-tools" role="img" aria-label="Hand riveting tool with nosepieces"></div><span class="pill">Riveting Tools</span></div>
  <div class="abs side"><div class="side-head">CATEGORIES</div><div class="side-search">search wines<b></b></div><ul><li>ALL</li><li>BLIND RIVETS</li><li>BLIND RIVET NUT</li><li>RIVETING TOOLS</li><li>LOREM IPSUM SED</li><li>LOREM IPSUM SED</li><li>LOREM IPSUM SED</li></ul></div>
  <div class="abs feat-line" style="left:294px;width:140px"></div>
  <div class="abs feat-title">FEATURED PRODUCTS</div>
  <div class="abs feat-line" style="left:675px;width:142px"></div>
  <div class="abs card" style="left:272px;top:977px"><span class="sku"># 12242</span><svg class="heart" width="14" height="12" viewBox="0 0 24 21"><path fill="#ddd" d="M12 21L2 11A6 6 0 0112 3a6 6 0 0110 8z"/></svg><div class="pic pic-gun" role="img" aria-label="Battery-driven rivet tool"></div><div class="name">Battery-Driven</div><div class="stars">★★★★★</div><div class="bar"><div class="qty"><span>–</span><span>1</span><span style="border:0">+</span></div><div class="add">🛒 ADD TO CART</div></div></div>
  <div class="abs card" style="left:456px;top:977px"><span class="sku"># 12242</span><svg class="heart" width="14" height="12" viewBox="0 0 24 21"><path fill="#ddd" d="M12 21L2 11A6 6 0 0112 3a6 6 0 0110 8z"/></svg><div class="pic pic-rivet" role="img" aria-label="Single blind rivet"></div><div class="name">blind-rivets</div><div class="stars">★★★★★</div><div class="bar"><div class="qty"><span>–</span><span>1</span><span style="border:0">+</span></div><div class="add">🛒 ADD TO CART</div></div></div>
  <div class="abs card" style="left:640px;top:977px"><span class="sku"># 12242</span><svg class="heart" width="14" height="12" viewBox="0 0 24 21"><path fill="#ddd" d="M12 21L2 11A6 6 0 0112 3a6 6 0 0110 8z"/></svg><div class="pic pic-nut" role="img" aria-label="Knurled blind rivet nut"></div><div class="name">blind-rivet-nut</div><div class="stars">★★★★★</div><div class="bar"><div class="qty"><span>–</span><span>1</span><span style="border:0">+</span></div><div class="add">🛒 ADD TO CART</div></div></div>
  <div class="abs card" style="left:272px;top:1281px"><span class="sku"># 12242</span><svg class="heart" width="14" height="12" viewBox="0 0 24 21"><path fill="#ddd" d="M12 21L2 11A6 6 0 0112 3a6 6 0 0110 8z"/></svg><div class="pic pic-pin" role="img" aria-label="Blind rivet with mandrel"></div><div class="name">Battery-Driven</div><div class="stars">★★★★★</div><div class="bar"><div class="qty"><span>–</span><span>1</span><span style="border:0">+</span></div><div class="add">🛒 ADD TO CART</div></div></div>
  <div class="abs card" style="left:456px;top:1281px"><span class="sku"># 12242</span><svg class="heart" width="14" height="12" viewBox="0 0 24 21"><path fill="#ddd" d="M12 21L2 11A6 6 0 0112 3a6 6 0 0110 8z"/></svg><div class="pic pic-plier" role="img" aria-label="Orange hand riveter pliers"></div><div class="name">Battery-Driven</div><div class="stars">★★★★★</div><div class="bar"><div class="qty"><span>–</span><span>1</span><span style="border:0">+</span></div><div class="add">🛒 ADD TO CART</div></div></div>
  <div class="abs card" style="left:640px;top:1281px"><span class="sku"># 12242</span><svg class="heart" width="14" height="12" viewBox="0 0 24 21"><path fill="#ddd" d="M12 21L2 11A6 6 0 0112 3a6 6 0 0110 8z"/></svg><div class="pic pic-gun" role="img" aria-label="Battery-driven rivet tool"></div><div class="name">Battery-Driven</div><div class="stars">★★★★★</div><div class="bar"><div class="qty"><span>–</span><span>1</span><span style="border:0">+</span></div><div class="add">🛒 ADD TO CART</div></div></div>
  <footer class="abs footer">
    <div class="fcol" style="left:83px"><h4>INFORMATION</h4><p>About Us<br>Contact US<br>Terms Of Use<br>Privacy Policy</p></div>
    <div class="fcol" style="left:257px"><h4>CONTACT &amp; SUPPORT</h4><p>sales and support:<br>+ 45 20 11 48 90<br>+ 45 20 11 48 91<br>E-mail: rivetline.example</p></div>
    <div class="fcol" style="left:471px"><h4>WHY CHOOSE US</h4><p>Product Recall<br>Gift Vouchers<br>Returns And Exchanges<br>Shipping Options</p></div>
    <div class="fcol" style="left:675px"><h4>POPULAR CATEGORY</h4><p>Lorem ipsum dolor sit amet,<br>Lorem ipsum dolor sit amet,<br>Lorem ipsum amet,<br>Lorem ipsum &nbsp;sit amet,</p></div>
    <div class="fdiv"></div>
    <div class="copy">Copyright © 2020. All Rights Reserved</div>
    <span class="pay" style="left:616px"></span><span class="pay" style="left:650px"></span><span class="pay" style="left:684px"></span><span class="pay" style="left:718px"></span><span class="pay" style="left:752px"></span><span class="pay" style="left:786px"></span>
  </footer>
</div>

</div>
</body>
</html>
```